Tall Fern Roofing Business Card

Need a business card with the logo that was designed here

Contact Information for Business Card

Name, Title, Phone, Email, Website, Company name

```html
<!DOCTYPE html>
<html lang="en">
<head>
<meta charset="UTF-8">
<title>Tall Fern Roofing – Business Card</title>
<link href="https://fonts.googleapis.com/css2?family=Poppins:wght@400;500;700&display=swap" rel="stylesheet">
<style>
  :root {
    --page-bg: #e9e7e6;
    --card-light: #f5f2f2;
    --brand-blue: #1c75bc;
    --divider-grey: #8c9096;
    --text-light: #ffffff;
  }
  * { margin: 0; padding: 0; box-sizing: border-box; }
  html, body {
    width: 1200px;
    height: 900px;
    overflow: hidden;
    background: var(--page-bg);
    font-family: "Poppins", sans-serif;
  }
  .canvas {
    width: 1200px;
    height: 900px;
    display: flex;
    align-items: center;
    justify-content: center;
  }
  .business-card {
    width: 960px;
    height: 594px;
    display: flex;
    box-shadow: 0 12px 36px rgba(0,0,0,0.18);
  }
  .card-front {
    width: 486px;
    background: var(--card-light);
    display: flex;
    align-items: center;
    justify-content: center;
  }
  .brand-mark {
    display: flex;
    align-items: center;
    gap: 14px;
  }
  .brand-square {
    width: 26px;
    height: 26px;
    background: var(--brand-blue);
  }
  .brand-name {
    color: var(--brand-blue);
    font-weight: 700;
    font-size: 38px;
    letter-spacing: 0.5px;
  }
  .card-divider {
    width: 7px;
    background: var(--divider-grey);
  }
  .card-back {
    flex: 1;
    background: var(--brand-blue);
    color: var(--text-light);
    padding: 186px 24px 0 24px;
  }
  .person-name {
    font-weight: 700;
    font-size: 33px;
    line-height: 1.1;
    letter-spacing: 0.2px;
  }
  .person-title {
    font-weight: 400;
    font-size: 26px;
    line-height: 1.2;
  }
  .contact-list {
    list-style: none;
    margin-top: 44px;
  }
  .contact-item {
    display: flex;
    align-items: center;
    gap: 12px;
    font-size: 26px;
    line-height: 35px;
  }
  .contact-icon {
    width: 26px;
    height: 26px;
    flex: none;
  }
</style>
</head>
<body>
<main class="canvas">
  <section class="business-card">
    <div class="card-front">
      <div class="brand-mark">
        <span class="brand-square"></span>
        <span class="brand-name">Tall Fern Roofing</span>
      </div>
    </div>
    <div class="card-divider"></div>
    <div class="card-back">
      <h1 class="person-name">DANIEL HARTLEY</h1>
      <p class="person-title">Managing Director</p>
      <ul class="contact-list">
        <li class="contact-item">
          <svg class="contact-icon" viewBox="0 0 24 24" fill="none" stroke="#fff" stroke-width="2" stroke-linecap="round" stroke-linejoin="round"><path d="M5 3h4l2 5-2.5 1.5a11 11 0 0 0 6 6L16 13l5 2v4a2 2 0 0 1-2 2A17 17 0 0 1 3 5a2 2 0 0 1 2-2z"/><path d="M15 3a6 6 0 0 1 6 6"/><path d="M15 7a2 2 0 0 1 2 2"/></svg>
          <span>044-987 654 321</span>
        </li>
        <li class="contact-item">
          <svg class="contact-icon" viewBox="0 0 24 24" fill="none" stroke="#fff" stroke-width="2" stroke-linejoin="round"><rect x="2" y="5" width="20" height="14"/><path d="M2 5l10 8 10-8"/><path d="M2 19l7-7M22 19l-7-7"/></svg>
          <span>hello@tallfernroofing.com</span>
        </li>
        <li class="contact-item">
          <svg class="contact-icon" viewBox="0 0 24 24" fill="none" stroke="#fff" stroke-width="1.8"><circle cx="12" cy="12" r="10"/><ellipse cx="12" cy="12" rx="4.5" ry="10"/><path d="M2 12h20M4 7h16M4 17h16"/></svg>
          <span>www.tallfernroofing.com</span>
        </li>
      </ul>
    </div>
  </section>
</main>
</body>
</html>
```